Verodex business card

Business card for sustainable investment company called "Verodex". Verodex is an exchange platform selling carbon credits between buyers and sellers. Carbon Credits are an environmental commodity for reducing global carbon emissions.

the card should obviously have our logo and the theme should be sustainability/environment mixed with a trading platform.

Contact Information for Business Card

Logo, Name, Title, Phone, Email

Colors
0054AA
0677BA
7BADD7
CADEEF
E8F1F8
0094D4
00A9DD
6FCCEA
C7EBF8
E9F6FB
00AB8E
00BBA5
67D7C9
C6EFE9
E9F9F6
59FF00
82FF00
B8FF75
E3FFCB
F4FFEA

```html
<!DOCTYPE html>
<html lang="en">
<head>
<meta charset="utf-8">
<title>Verodex business card</title>
<link rel="stylesheet" href="https://fonts.googleapis.com/css2?family=Montserrat:wght@600;700&family=Open+Sans:wght@400;600&display=swap">
<style>
  :root {
    --stage: #1c1d21;
    --navy: #142b55;
    --navy-deep: #102347;
    --map-tone: #2a4a7a;
    --cyan: #5cc4e0;
    --sky-top: #4a7dc6;
    --sky-bottom: #66cbdb;
    --white: #ffffff;
    --accent-bar: #6fa6dc;
  }
  * { margin: 0; padding: 0; box-sizing: border-box; }
  html, body { width: 1200px; height: 780px; overflow: hidden; }
  body {
    background: var(--stage);
    display: flex;
    align-items: center;
    justify-content: center;
    gap: 40px;
  }
  .card {
    position: relative;
    width: 540px;
    height: 310px;
    background: var(--navy);
    overflow: hidden;
    box-shadow: 0 18px 40px rgba(0,0,0,0.45);
  }

  /* Back face */
  .card-back .world-map {
    position: absolute;
    left: 40px; top: 28px;
    width: 470px; height: 250px;
    border-radius: 40px;
    background: radial-gradient(ellipse at center, var(--map-tone) 0%, rgba(42,74,122,0.55) 55%, rgba(20,43,85,0) 80%);
  }
  .brand {
    position: absolute;
    display: flex;
    align-items: center;
    gap: 16px;
  }
  .brand-dot {
    width: 46px; height: 46px;
    border-radius: 50%;
    background: var(--cyan);
  }
  .brand-name {
    font-family: "Montserrat", sans-serif;
    font-weight: 700;
    color: var(--white);
    letter-spacing: 0.06em;
    text-transform: uppercase;
  }
  .card-back .brand { left: 120px; top: 128px; }
  .card-back .brand-name { font-size: 46px; }

  /* Front face */
  .card-front .sky-wave {
    position: absolute; inset: 0;
    width: 540px; height: 310px;
  }
  .card-front .brand { left: 34px; top: 136px; gap: 12px; }
  .card-front .brand-dot { width: 32px; height: 32px; }
  .card-front .brand-name { font-size: 32px; }

  .accent-bar {
    position: absolute;
    right: 0; top: 10px;
    width: 22px; height: 30px;
    background: var(--accent-bar);
  }
  .holder {
    position: absolute;
    right: 30px; top: 12px;
    text-align: right;
  }
  .holder-name {
    font-family: "Montserrat", sans-serif;
    font-weight: 700;
    font-size: 27px;
    color: var(--cyan);
    line-height: 1.1;
  }
  .holder-title {
    font-family: "Open Sans", sans-serif;
    font-weight: 600;
    font-size: 13px;
    color: var(--white);
    letter-spacing: 0.02em;
  }
  .contact {
    position: absolute;
    right: 22px; top: 132px;
    font-family: "Open Sans", sans-serif;
    font-size: 13px;
    color: var(--white);
    text-align: right;
    line-height: 1.35;
    list-style: none;
  }
  .contact .address { margin-bottom: 8px; }
  .contact li { display: flex; justify-content: flex-end; align-items: center; gap: 6px; }
  .contact svg { width: 12px; height: 12px; flex: none; }
</style>
</head>
<body>

  <section class="card card-back" aria-label="Verodex card, back">
    <div class="world-map" role="img" aria-label="Dotted world map in faint blue across the card"></div>
    <div class="brand">
      <span class="brand-dot"></span>
      <span class="brand-name">Verodex</span>
    </div>
  </section>

  <section class="card card-front" aria-label="Verodex card, front">
    <svg class="sky-wave" viewBox="0 0 540 310" aria-hidden="true">
      <defs>
        <linearGradient id="skyGradient" x1="0" y1="0" x2="0" y2="1">
          <stop offset="0" stop-color="#4a7dc6"/>
          <stop offset="1" stop-color="#66cbdb"/>
        </linearGradient>
      </defs>
      <path d="M540,70 C420,74 345,100 322,150 C302,196 290,240 240,262 C180,288 90,286 0,270 L0,310 L540,310 Z" fill="url(#skyGradient)"/>
      <path d="M450,86 C380,100 335,122 316,160 C298,205 284,246 234,268 C176,290 90,290 20,278" fill="none" stroke="#ffffff" stroke-width="5" stroke-linecap="round"/>
    </svg>

    <div class="accent-bar"></div>
    <header class="holder">
      <p class="holder-name">Marta Kolarova</p>
      <p class="holder-title">Managing Director</p>
    </header>

    <div class="brand">
      <span class="brand-dot"></span>
      <span class="brand-name">Verodex</span>
    </div>

    <ul class="contact">
      <li class="address">1840 Linden Ave. Suite 310<br>Ashford, TX 75219</li>
      <li>(555) 214-6083
        <svg viewBox="0 0 12 12"><path d="M3 1 L5 3.5 L4 4.8 C4.6 6.3 5.7 7.4 7.2 8 L8.5 7 L11 9 L9.8 10.8 C5.5 10.5 1.5 6.5 1.2 2.2 Z" fill="#ffffff"/></svg>
      </li>
      <li>info@verodex.com
        <svg viewBox="0 0 12 12"><rect x="1" y="2.5" width="10" height="7" fill="none" stroke="#ffffff" stroke-width="1.2"/><path d="M1 2.5 L6 6.5 L11 2.5" fill="none" stroke="#ffffff" stroke-width="1.2"/></svg>
      </li>
      <li>www.verodex.com
        <svg viewBox="0 0 12 12"><circle cx="6" cy="6" r="5" fill="none" stroke="#ffffff" stroke-width="1.1"/><ellipse cx="6" cy="6" rx="2.2" ry="5" fill="none" stroke="#ffffff" stroke-width="1"/><path d="M1 6 H11" stroke="#ffffff" stroke-width="1"/></svg>
      </li>
    </ul>
  </section>

</body>
</html>
```